Business card design for Automotive workshop

We need a business card for a new automotive repair and tyre shop called Keelstone Prime Automotive located in New Zealand. We are a clean, modern and fresh workshop and company.

Front needs to feature logo,
my name:
Marlo Fenwicke (director)

Address:
48 Tarn Lane
Korimako Bay 3592

Phone: 07 594 2713
Mobile: 027 451 9362
Email: office@keelstoneautomotive.example.nz
Website: keelstoneautomotive.example.nz

Back needs to feature an area to write down appointment details, date and time.

Also feature a list of jobs and work we do such as,
Vehicle Servicing
All Mechanical Repairs
Warrant of Fitness
Tyres & Wheel Alignments
Automotive Diagnostics
Automotive Parts & Supplies

```html
<!DOCTYPE html>
<html lang="en">
<head>
<meta charset="utf-8">
<title>Keelstone Prime Automotive – Business Card</title>
<link rel="stylesheet" href="https://fonts.googleapis.com/css2?family=Lato:wght@400;700;900&family=Roboto:wght@500&display=swap">
<style>
  :root {
    --red: #e3202a;
    --charcoal: #3e3e40;
    --ink: #4a4a4a;
    --paper: #ffffff;
    --backdrop: #e6e6e8;
    --rule: #9a9a9a;
  }
  * { box-sizing: border-box; margin: 0; padding: 0; }
  html, body { width: 1200px; height: 912px; overflow: hidden; }
  body {
    background: var(--backdrop);
    font-family: "Lato", sans-serif;
    color: var(--ink);
    display: flex;
    align-items: center;
    justify-content: center;
    gap: 40px;
  }
  .card {
    position: relative;
    width: 540px;
    height: 330px;
    border-radius: 18px;
    background: var(--paper);
    overflow: hidden;
    box-shadow: 0 10px 30px rgba(0,0,0,.18);
  }

  .brand {
    font-family: "Lato", sans-serif;
    font-weight: 900;
    color: var(--red);
    letter-spacing: 1px;
    text-transform: uppercase;
    line-height: 1.05;
  }

  /* Back side */
  .card-back__top {
    position: absolute;
    inset: 0 0 auto 0;
    height: 188px;
    background: var(--charcoal);
    border-bottom: 4px solid var(--red);
    display: flex;
    flex-direction: column;
    align-items: center;
    padding-top: 34px;
  }
  .card-back .brand { font-size: 26px; text-align: center; }
  .services {
    margin-top: 20px;
    color: #f2f2f2;
    font-size: 14px;
    line-height: 1.55;
    text-align: center;
  }
  .services .sep { color: var(--red); padding: 0 4px; }
  .appointment {
    position: absolute;
    top: 212px;
    left: 0; right: 0;
    text-align: center;
    color: var(--red);
    font-size: 15px;
  }
  .appointment-fields {
    position: absolute;
    left: 36px; right: 36px;
    top: 248px;
    display: flex;
    gap: 12px;
    font-size: 15px;
    color: var(--ink);
  }
  .field { display: flex; align-items: flex-end; flex: 1; gap: 6px; }
  .field__line { flex: 1; border-bottom: 1px solid var(--rule); height: 16px; }

  /* Front side */
  .card-front .brand {
    position: absolute;
    top: 34px; right: 32px;
    font-size: 22px;
    text-align: right;
  }
  .person { position: absolute; left: 38px; top: 150px; }
  .person__name {
    font-family: "Roboto", sans-serif;
    font-weight: 500;
    font-size: 30px;
    color: var(--red);
    line-height: 1;
  }
  .person__role { font-size: 16px; color: var(--ink); margin-top: 4px; }
  .divider {
    position: absolute;
    left: 38px; right: 30px; top: 210px;
    border-top: 1px solid var(--red);
  }
  .contacts {
    position: absolute;
    left: 56px; top: 222px;
    list-style: none;
    font-size: 15px;
    line-height: 1.4;
  }
  .contacts li { display: flex; align-items: center; gap: 8px; }
  .contacts svg { width: 11px; height: 11px; flex: none; }
  .address {
    position: absolute;
    right: 32px; top: 222px;
    font-size: 15px;
    line-height: 1.4;
    text-align: right;
  }
</style>
</head>
<body>

  <section class="card card-back" aria-label="Card back">
    <div class="card-back__top">
      <p class="brand">Keelstone Prime<br>Automotive</p>
      <p class="services">
        Vehicle Servicing<span class="sep">|</span>All Mechanical Repairs<br>
        Warrant of Fitness<span class="sep">|</span>Tyres &amp; Wheel Alignments<br>
        Automotive Diagnostics<span class="sep">|</span>Automotive Parts &amp; Supplies
      </p>
    </div>
    <p class="appointment">Appointment</p>
    <div class="appointment-fields">
      <div class="field"><span>Date</span><span class="field__line"></span></div>
      <div class="field"><span>Time</span><span class="field__line"></span></div>
    </div>
  </section>

  <section class="card card-front" aria-label="Card front">
    <p class="brand">Keelstone Prime<br>Automotive</p>
    <div class="person">
      <p class="person__name">Marlo Fenwicke</p>
      <p class="person__role">Director</p>
    </div>
    <div class="divider"></div>
    <ul class="contacts">
      <li>
        <svg viewBox="0 0 12 12" aria-hidden="true"><path d="M2 1h2.5l1 3-1.5 1a6 6 0 0 0 3 3l1-1.5 3 1V10a1 1 0 0 1-1 1A10 10 0 0 1 1 2a1 1 0 0 1 1-1z" fill="var(--red)"/></svg>
        07 594 2713
      </li>
      <li>
        <svg viewBox="0 0 12 12" aria-hidden="true"><rect x="3" y="0.5" width="6" height="11" rx="1.2" fill="none" stroke="var(--red)" stroke-width="1.3"/><circle cx="6" cy="9.3" r=".8" fill="var(--red)"/></svg>
        027 451 9362
      </li>
      <li>
        <svg viewBox="0 0 12 12" aria-hidden="true"><rect x="0.7" y="2.2" width="10.6" height="7.6" rx="1" fill="none" stroke="var(--red)" stroke-width="1.3"/><path d="M1 3l5 3.6L11 3" fill="none" stroke="var(--red)" stroke-width="1.2"/></svg>
        office@keelstoneautomotive.example.nz
      </li>
      <li>
        <svg viewBox="0 0 12 12" aria-hidden="true"><circle cx="6" cy="6" r="5.2" fill="none" stroke="var(--red)" stroke-width="1.2"/><ellipse cx="6" cy="6" rx="2.2" ry="5.2" fill="none" stroke="var(--red)" stroke-width="1"/><path d="M1 6h10" stroke="var(--red)" stroke-width="1"/></svg>
        www.keelstoneautomotive.example.nz
      </li>
    </ul>
    <p class="address">48 Tarn Lane<br>Korimako Bay 3592</p>
  </section>

</body>
</html>
```